Business Cards for IT Consulting Company (Managed Service Provider)

I am looking to have some business cards printed and would like some designs. We are an IT Consulting company based in Vancouver BC. I would like a nice clean and modern look to the cards. I have uploaded all the versions of my logo so parts can be used as needed. Here is a snippit from our website homepage:

Quillbrook Networks Ltd. is an IT Solutions Partner located in Vancouver BC, Canada. We offer IT solutions and support to customers in the greater Vancouver Area. With expertise in Microsoft platforms, as well as Linux and Mac OSX and over 12 years experience in the IT industry, Quillbrook Networks is dedicated to offering our clients top quality service and products. We take pride in the solutions we offer our customers. The greatest compliment a client can give us is to recommend our services.

Quillbrook Networks Ltd. offers a wide range of IT services from onsite service to remote support and managed service solutions. This allows clients to choose the support path that best suits their company’s needs. Supporting many different sized companies from small to enterprise level over the past 12 years Quillbrook Networks has the experience and expertise needed to ensure things run smoothly. Allowing our clients to focus on doing business.

Revolutionizing the way IT services are delivered.

Quillbrook Networks is dedicated to providing our clients with IT solutions that work and grow with them for years to come. This philosophy helps save money in the long run instead of replacing equipment constantly. Far too often IT solutions are not well thought out and while possibly solving the problem at hand, require replacement due to growth or quality within a very short time frame. Quillbrook Networks takes pride in providing solutions that will last and be able to accommodate growth without the need for replacement.

Industry/Entity Type

Information Technology

Contact Information for Business Card

Quillbrook Networks Ltd.
(Employee Name)
Eml: (Employees Email Address)
Web: quillbrook.me
Ph: 604-555-0148

Font styles to use
Serif
Sans Serif

Requirements
Must have
• The Company logo and company colors.
Nice to have
• - Our tag line: "Revolutionizing IT Services" or "Revolutionizing the way IT services are delivered."
• - Also I really like the idea of nature and technology together blending which is sort of where my logo came from so integrating that somehow onto the business cards would be great.

```html
<!DOCTYPE html>
<html lang="en">
<head>
<meta charset="utf-8">
<title>Quillbrook Networks Ltd. – Business Cards</title>
<link rel="stylesheet" href="https://fonts.googleapis.com/css2?family=Open+Sans:wght@400;600;700&display=swap">
<style>
  :root {
    --backdrop: #4a433f;
    --card: #121213;
    --card-edge: #1c1c1e;
    --brand-blue: #2a9fe2;
    --text-light: #e9eaec;
    --text-muted: #c9cbce;
    --divider: #6b6d72;
  }
  * { margin: 0; padding: 0; box-sizing: border-box; }
  html, body {
    width: 1200px; height: 814px; overflow: hidden;
    background: var(--backdrop);
    font-family: "Open Sans", Arial, sans-serif;
  }
  .canvas {
    position: relative; width: 1200px; height: 814px;
    display: flex; align-items: center; justify-content: center; gap: 56px;
  }
  .card {
    position: relative; width: 520px; height: 297px;
    background: var(--card);
    border: 1px solid var(--card-edge);
    box-shadow: 0 14px 30px rgba(0,0,0,.35);
  }
  .brand {
    display: flex; align-items: center; gap: 12px;
    color: var(--brand-blue); font-weight: 700; white-space: nowrap;
  }
  .brand-square {
    width: 26px; height: 26px; background: var(--brand-blue); flex: none;
  }
  /* Contact side */
  .card-front .brand {
    position: absolute; top: 70px; left: 0; right: 0;
    justify-content: center; font-size: 27px;
  }
  .details {
    position: absolute; top: 150px; left: 0; right: 0;
    display: flex; justify-content: center;
  }
  .person {
    text-align: right; padding-right: 22px;
    border-right: 1px solid var(--divider);
    color: var(--text-muted); font-size: 15px; line-height: 1.45;
  }
  .person-name {
    color: var(--brand-blue); font-weight: 600; font-size: 21px; line-height: 1.3;
  }
  .contact-list {
    list-style: none; padding-left: 22px; padding-top: 2px;
    color: var(--text-light); font-size: 14px; line-height: 1.75;
  }
  .contact-list li { display: flex; align-items: center; gap: 9px; }
  .contact-icon { width: 12px; height: 12px; flex: none; fill: var(--brand-blue); }
  /* Logo side */
  .card-back .brand {
    position: absolute; top: 98px; left: 0; right: 0;
    justify-content: center; font-size: 30px;
  }
  .tagline {
    position: absolute; top: 176px; left: 0; right: 0;
    text-align: center; color: var(--text-light);
    font-size: 13px; font-weight: 600;
  }
</style>
</head>
<body>
<main class="canvas">
  <section class="card card-front" aria-label="Business card, contact side">
    <div class="brand"><span class="brand-square"></span>Quillbrook Networks Ltd.</div>
    <div class="details">
      <div class="person">
        <p class="person-name">Daniel Marsh</p>
        <p>2140 Cedarview Lane</p>
        <p>Burnaby, BC V5G 1K3</p>
      </div>
      <ul class="contact-list">
        <li>
          <svg class="contact-icon" viewBox="0 0 24 24" aria-hidden="true"><path d="M6.6 10.8a15.2 15.2 0 0 0 6.6 6.6l2.2-2.2a1 1 0 0 1 1-.25 11.4 11.4 0 0 0 3.6.57 1 1 0 0 1 1 1V20a1 1 0 0 1-1 1A17 17 0 0 1 3 4a1 1 0 0 1 1-1h3.5a1 1 0 0 1 1 1c0 1.25.2 2.45.57 3.57a1 1 0 0 1-.25 1z"/></svg>
          604-555-0148
        </li>
        <li>
          <svg class="contact-icon" viewBox="0 0 24 24" aria-hidden="true"><path d="M2 5h20v14H2z M3.5 6.5 12 13l8.5-6.5" fill="none" stroke="#2a9fe2" stroke-width="2.4"/></svg>
          name@quillbrook.me
        </li>
        <li>
          <svg class="contact-icon" viewBox="0 0 24 24" aria-hidden="true"><circle cx="12" cy="12" r="10"/><path d="M2 12h20M12 2c3 3 3 17 0 20M12 2c-3 3-3 17 0 20" stroke="#121213" stroke-width="1.6" fill="none"/></svg>
          www.quillbrook.me
        </li>
      </ul>
    </div>
  </section>

  <section class="card card-back" aria-label="Business card, logo side">
    <div class="brand"><span class="brand-square"></span>Quillbrook Networks Ltd.</div>
    <p class="tagline">Revolutionizing IT Services</p>
  </section>
</main>
</body>
</html>
```